Fresh, modern, fun business card for pediatric dental practice

Need a business card for fresh, modern, fun pediatric dental practice

Clean look that matches our website's font and colors

We prefer the look of curved corners on business cards

Target Market(s)

parents (mothers) of young children, professionals, mid-high class

Industry/Entity Type

Dental

Contact Information for Business Card

Maplebrook Pediatric Dentistry
482 Quarry Lane
Suite 517
Alder Falls, PA 17599
717.555.0193
www.maplebrookkidsdental.example

Mei-Ran Tsai, DMD
Corinne Walbeck, DMD
(we are working on our email address, but we would like that on the card as well)

Font styles to use
Sans Serif

Requirements
Must have
• All info; we would also like to make cards for individual staff members
• colors from our website and color palatte, attatched
• use same font and design as website for branding
Nice to have
• clean, simple card that has a pop of color
• we would like to see a few designs with our tag line "where smiles get brighter"
• we are not sure if we want to have it on there or not
• we would like to see a few designs incorporating the ribbon graphic on our website where the word WELCOME is

```html
<!DOCTYPE html>
<html lang="en">
<head>
<meta charset="utf-8">
<title>Maplebrook Pediatric Dentistry – Business Card</title>
<link href="https://fonts.googleapis.com/css2?family=Work+Sans:wght@400;500;600;700&display=swap" rel="stylesheet">
<style>
  :root {
    --bg: #2b2724;
    --card: #1d1d1f;
    --yellow: #fdb515;
    --magenta: #d63ab4;
    --gold-line: #b8860b;
    --white: #f2f2f2;
  }
  * { box-sizing: border-box; margin: 0; padding: 0; }
  html, body { width: 1200px; height: 715px; overflow: hidden; }
  body {
    background: var(--bg);
    font-family: "Work Sans", Arial, sans-serif;
    position: relative;
  }
  .card {
    position: absolute;
    top: 209px;
    width: 520px;
    height: 297px;
    background: var(--card);
    border-radius: 16px;
    overflow: hidden;
  }
  .card--front { left: 50px; }
  .card--back { left: 630px; }

  .brand {
    display: flex;
    align-items: center;
    gap: 12px;
    color: var(--yellow);
    font-weight: 600;
    line-height: 1;
  }
  .brand__dot {
    width: 18px; height: 18px;
    border-radius: 50%;
    background: var(--yellow);
    flex: none;
  }
  .brand__name { display: flex; flex-direction: column; gap: 6px; }
  .brand__main { letter-spacing: 0.5px; }
  .brand__sub { letter-spacing: 1.5px; }

  .card--front .brand {
    position: absolute; left: 0; right: 0; top: 108px;
    justify-content: center;
  }
  .card--front .brand__main { font-size: 46px; }
  .card--front .brand__sub { font-size: 20px; }

  .card--back .brand { position: absolute; left: 120px; top: 40px; }
  .card--back .brand__main { font-size: 34px; }
  .card--back .brand__sub { font-size: 15px; }

  .rule {
    position: absolute; left: 80px; top: 170px;
    width: 410px; height: 1px; background: var(--gold-line);
  }
  .person {
    position: absolute; right: 30px; top: 142px;
    text-align: right;
  }
  .person__name {
    color: var(--yellow); font-weight: 700; font-size: 18px; letter-spacing: 0.5px;
  }
  .person__title {
    color: var(--white); font-size: 10px; margin-top: 10px; letter-spacing: 1px;
  }
  .contacts {
    position: absolute; left: 26px; top: 182px;
    list-style: none; color: var(--white); font-size: 11px;
  }
  .contacts li { display: flex; align-items: center; gap: 8px; height: 17px; }
  .contacts svg { width: 9px; height: 9px; flex: none; }
  .address {
    position: absolute; right: 30px; top: 206px;
    text-align: right; color: var(--white); font-size: 12.5px; line-height: 17px;
    font-style: normal;
  }
  .bands { position: absolute; left: 0; top: 0; }
</style>
</head>
<body>

  <section class="card card--front" aria-label="Card front">
    <div class="brand">
      <span class="brand__dot"></span>
      <span class="brand__name">
        <span class="brand__main">maplebrook</span>
        <span class="brand__sub">pediatric dentistry</span>
      </span>
    </div>
  </section>

  <section class="card card--back" aria-label="Card back">
    <svg class="bands" width="520" height="297" viewBox="0 0 520 297" aria-hidden="true">
      <rect x="0" y="254" width="330" height="4" fill="var(--magenta)"/>
      <path d="M0 262 L330 262 C352 262 356 278 380 278 L520 278 L520 297 L0 297 Z" fill="var(--yellow)"/>
    </svg>

    <div class="brand">
      <span class="brand__dot"></span>
      <span class="brand__name">
        <span class="brand__main">maplebrook</span>
        <span class="brand__sub">pediatric dentistry</span>
      </span>
    </div>

    <div class="rule"></div>

    <div class="person">
      <div class="person__name">CORINNE WALBECK</div>
      <div class="person__title">DMD</div>
    </div>

    <ul class="contacts">
      <li>
        <svg viewBox="0 0 10 10"><path d="M2 1 L4 1 L4.5 3 L3.3 3.8 C3.8 5 5 6.2 6.2 6.7 L7 5.5 L9 6 L9 8 C5 8.5 1.5 5 2 1 Z" fill="var(--yellow)"/></svg>
        717.555.0193
      </li>
      <li>
        <svg viewBox="0 0 10 10"><rect x="1" y="2" width="8" height="6" fill="none" stroke="var(--yellow)" stroke-width="1"/><path d="M1 2 L5 5.5 L9 2" fill="none" stroke="var(--yellow)" stroke-width="1"/></svg>
        hello@maplebrookkidsdental.example
      </li>
      <li>
        <svg viewBox="0 0 10 10"><circle cx="5" cy="5" r="4" fill="none" stroke="var(--yellow)" stroke-width="1"/><path d="M1 5 H9 M5 1 C3 3.5 3 6.5 5 9 M5 1 C7 3.5 7 6.5 5 9" fill="none" stroke="var(--yellow)" stroke-width="0.8"/></svg>
        www.maplebrookkidsdental.example
      </li>
    </ul>

    <address class="address">
      482 Quarry Lane<br>
      Suite 517 Alder Falls, PA 17599
    </address>
  </section>

</body>
</html>
```